Business card design for Virtual Assistance company

I need a business card designed for my virtual assistance company. We are a small company who services primarily C-level executive clients. The card needs to be double sided with the following contact information on the back:
Melissa Thornbury
Owner/CEO
info@rkpadvisory.net
www.rkpadvisory.net
555.302.9817

The front side should just have the company name incorporated: "RKP Advisory" and "virtual assistance"

The card should be simplistic, but eye catching and should speak to high level executives. Our primary focus areas consist of executive assistance and government contracting.

Target Market(s)

CEOs and executives

Contact Information for Business Card

see project description. phone, email, website.

Colors

Designer to choose only greyscale colors for use in the design.

```html
<!DOCTYPE html>
<html lang="en">
<head>
<meta charset="utf-8">
<title>RKP Advisory – Business Card</title>
<link href="https://fonts.googleapis.com/css2?family=Cinzel:wght@400;600&family=Poppins:wght@400&display=swap" rel="stylesheet">
<style>
  :root {
    --charcoal: #2e2e2e;
    --white: #ffffff;
    --grey: #9a9a9a;
    --ink: #3a3a3a;
    --backdrop: #e6e6e6;
  }
  * { margin: 0; padding: 0; box-sizing: border-box; }
  html, body { width: 1200px; height: 900px; overflow: hidden; }
  body {
    background: var(--backdrop);
    display: flex;
    flex-direction: column;
    align-items: center;
    justify-content: center;
    gap: 46px;
    font-family: "Poppins", sans-serif;
  }
  .card {
    position: relative;
    width: 660px;
    height: 377px;
    box-shadow: 0 8px 22px rgba(0,0,0,.22);
    overflow: hidden;
  }

  /* Front side */
  .card--front {
    background: var(--charcoal);
    color: var(--white);
    display: flex;
    flex-direction: column;
    align-items: center;
    justify-content: center;
  }
  .brand-name {
    font-family: "Cinzel", serif;
    font-weight: 600;
    font-size: 60px;
    letter-spacing: 2px;
    line-height: 1;
  }
  .tagline {
    display: flex;
    align-items: center;
    gap: 14px;
    margin-top: 18px;
    font-family: "Cinzel", serif;
    font-size: 16px;
    letter-spacing: 4px;
    text-transform: uppercase;
  }
  .tagline::before, .tagline::after {
    content: "";
    width: 46px;
    height: 1.5px;
    background: var(--white);
  }

  /* Back side */
  .card--back { background: var(--white); }
  .card__wave { position: absolute; inset: 0; }
  .holder {
    position: absolute;
    left: 44px;
    top: 84px;
  }
  .holder__name {
    font-family: "Cinzel", serif;
    font-weight: 600;
    font-size: 22px;
    color: var(--charcoal);
    letter-spacing: 1px;
    text-transform: uppercase;
    white-space: nowrap;
  }
  .holder__role {
    font-size: 15px;
    color: var(--ink);
    margin-top: 2px;
  }
  .back-brand {
    position: absolute;
    right: 36px;
    top: 50px;
    font-family: "Cinzel", serif;
    font-weight: 600;
    font-size: 30px;
    color: var(--charcoal);
    letter-spacing: 1px;
    white-space: nowrap;
  }
  .contact-list {
    position: absolute;
    left: 58px;
    top: 150px;
    list-style: none;
    font-size: 16px;
    color: var(--ink);
  }
  .contact-list li {
    display: flex;
    align-items: center;
    gap: 10px;
    height: 24px;
  }
  .contact-list svg { width: 16px; height: 16px; fill: var(--charcoal); }
  .contact-list .accent { color: var(--charcoal); }
  .back-tagline {
    position: absolute;
    right: 44px;
    bottom: 92px;
    font-size: 15px;
    letter-spacing: 1px;
    color: var(--white);
    text-transform: uppercase;
  }
</style>
</head>
<body>

  <section class="card card--front" aria-label="Card front">
    <div class="brand-name">RKP Advisory</div>
    <div class="tagline">Virtual Assistance</div>
  </section>

  <section class="card card--back" aria-label="Card back">
    <svg class="card__wave" viewBox="0 0 660 377" preserveAspectRatio="none" aria-hidden="true">
      <path d="M0,276 C210,280 380,220 520,148 C400,226 230,296 0,300 Z" fill="var(--grey)"/>
      <path d="M0,306 C240,304 440,190 660,118 L660,377 L0,377 Z" fill="var(--charcoal)"/>
    </svg>

    <div class="holder">
      <div class="holder__name">Melissa Thornbury</div>
      <div class="holder__role">Owner/CEO</div>
    </div>

    <div class="back-brand">RKP Advisory</div>

    <ul class="contact-list">
      <li>
        <svg viewBox="0 0 24 24"><path d="M6.6 10.8a15.1 15.1 0 0 0 6.6 6.6l2.2-2.2a1 1 0 0 1 1-.25 11.4 11.4 0 0 0 3.6.57 1 1 0 0 1 1 1V20a1 1 0 0 1-1 1A17 17 0 0 1 3 4a1 1 0 0 1 1-1h3.5a1 1 0 0 1 1 1c0 1.25.2 2.45.57 3.57a1 1 0 0 1-.25 1z"/></svg>
        555.302.9817
      </li>
      <li>
        <svg viewBox="0 0 24 24"><path d="M2 5h20v14H2z M4 7v.4l8 5.2 8-5.2V7z" fill-rule="evenodd"/></svg>
        <span>info@<span class="accent">rkpadvisory.net</span></span>
      </li>
      <li>
        <svg viewBox="0 0 24 24"><path d="M12 2a10 10 0 1 0 0 20 10 10 0 0 0 0-20zm6.9 6h-2.9a15.6 15.6 0 0 0-1.4-3.6A8 8 0 0 1 18.9 8zM12 4a14 14 0 0 1 1.9 4h-3.8A14 14 0 0 1 12 4zM4.3 14a8 8 0 0 1 0-4h3.4a16.5 16.5 0 0 0 0 4zm.8 2h2.9a15.6 15.6 0 0 0 1.4 3.6A8 8 0 0 1 5.1 16zM8 8H5.1a8 8 0 0 1 4.3-3.6A15.6 15.6 0 0 0 8 8zm4 12a14 14 0 0 1-1.9-4h3.8A14 14 0 0 1 12 20zm2.3-6H9.7a14.7 14.7 0 0 1 0-4h4.6a14.7 14.7 0 0 1 0 4zm.3 5.6a15.6 15.6 0 0 0 1.4-3.6h2.9a8 8 0 0 1-4.3 3.6zm1.7-5.6a16.5 16.5 0 0 0 0-4h3.4a8 8 0 0 1 0 4z"/></svg>
        <span>www.<span class="accent">rkpadvisory.net</span></span>
      </li>
    </ul>

    <div class="back-tagline">Virtual Assistance</div>
  </section>

</body>
</html>
```